SkyvornQ Business Cards and Stationary Design

Need a design for our business cards and stationary. I want to carry on the theme of the logo. I want the business cards to have a design on the back. I would like the business cards and the stationary to carry the same theme, design scheme, and branding

Target Market(s)

Airlines and Maintenance Facilities

Industry/Entity Type

Aviation

Contact Information for Business Card

Name
Position Title
Address: 4827 Trellis Hollow Road, Fort Pierce, Florida, 34951
Office Number
Mobile Number
Email
Website

Font styles to use
Serif
Sans Serif

Colors

Designer to choose colors to be used in the design.

```html
<!DOCTYPE html>
<html lang="en">
<head>
<meta charset="utf-8">
<title>SkyvornQ Business Card</title>
<link href="https://fonts.googleapis.com/css2?family=Roboto:wght@400;500;700;900&display=swap" rel="stylesheet">
<style>
  :root {
    --page: #e9e6e1;
    --navy: #0b2a57;
    --navy-deep: #071f45;
    --blue: #1f6fc0;
    --sky: #35aee8;
    --white: #ffffff;
    --paper: #f6f6f6;
  }
  * { box-sizing: border-box; margin: 0; padding: 0; }
  html, body {
    width: 1200px; height: 950px; overflow: hidden;
    background: var(--page);
    font-family: "Roboto", Arial, sans-serif;
  }
  .stage { position: relative; width: 1200px; height: 950px; }
  .card {
    position: absolute; top: 145px;
    width: 400px; height: 660px;
    border-radius: 26px; overflow: hidden;
    box-shadow: 0 10px 28px rgba(0,0,0,0.18);
  }
  .card--front { left: 160px; background: var(--paper); }
  .card--back { left: 640px; background: var(--navy); }

  .card__wave { position: absolute; inset: 0; }

  .brand {
    position: absolute; top: 80px; left: 0; right: 0;
    display: flex; flex-direction: column; align-items: center; gap: 18px;
  }
  .brand__dot {
    width: 62px; height: 62px; border-radius: 50%;
    background: var(--blue);
  }
  .brand__name {
    font-weight: 900; font-size: 40px; letter-spacing: 6px;
    color: var(--navy); text-transform: uppercase;
  }

  .contact {
    position: absolute; right: 30px; top: 420px;
    text-align: right; color: var(--white);
  }
  .contact__name { font-weight: 700; font-size: 26px; letter-spacing: 1px; }
  .contact__title { font-weight: 500; font-size: 18px; margin-bottom: 12px; }
  .contact__address { font-size: 16px; line-height: 1.3; margin-bottom: 14px; }
  .contact__line {
    display: flex; justify-content: flex-end; align-items: center; gap: 10px;
    font-size: 16px; line-height: 1.55;
  }
  .contact__icon { width: 16px; height: 16px; flex: none; }

  .back__url {
    position: absolute; left: 16px; top: 60px;
    writing-mode: vertical-rl;
    color: var(--white); font-size: 14px; letter-spacing: 7px;
  }
  .back__mark {
    position: absolute; left: 0; right: 0; top: 240px;
    display: flex; flex-direction: column; align-items: center; gap: 22px;
  }
  .back__dot {
    width: 110px; height: 110px; border-radius: 50%;
    border: 12px solid var(--white);
  }
  .back__name {
    font-weight: 900; font-size: 34px; letter-spacing: 6px;
    color: var(--white); text-transform: uppercase;
  }
</style>
</head>
<body>
<main class="stage">

  <section class="card card--front">
    <svg class="card__wave" viewBox="0 0 400 660" preserveAspectRatio="none" aria-hidden="true">
      <defs>
        <radialGradient id="frontGlow" cx="0.35" cy="0.75" r="0.8">
          <stop offset="0" stop-color="#35aee8"/>
          <stop offset="0.55" stop-color="#1f6fc0"/>
          <stop offset="1" stop-color="#0d3e86"/>
        </radialGradient>
      </defs>
      <path d="M0,350 C110,300 250,330 400,262 L400,660 L0,660 Z" fill="#0b2a57"/>
      <path d="M0,372 C120,322 255,350 400,286 L400,660 L0,660 Z" fill="url(#frontGlow)"/>
    </svg>

    <div class="brand">
      <span class="brand__dot"></span>
      <span class="brand__name">SkyvornQ</span>
    </div>

    <div class="contact">
      <p class="contact__name">DARREN HOLT</p>
      <p class="contact__title">CEO/FOUNDER</p>
      <p class="contact__address">4827 Trellis Hollow Road<br>Fort Pierce, Florida, 34951</p>
      <p class="contact__line">772 418 3096
        <svg class="contact__icon" viewBox="0 0 16 16"><path d="M4 1l3 3-2 2c1 2 3 4 5 5l2-2 3 3-2 3C7 15 1 9 1 3z" fill="#fff"/></svg>
      </p>
      <p class="contact__line">772 559 2147
        <svg class="contact__icon" viewBox="0 0 16 16"><rect x="4" y="1" width="8" height="14" rx="1.5" fill="none" stroke="#fff" stroke-width="1.6"/></svg>
      </p>
      <p class="contact__line">info@skyvornq.com
        <svg class="contact__icon" viewBox="0 0 16 16"><rect x="1" y="3" width="14" height="10" fill="#fff"/><path d="M1 3l7 6 7-6" fill="none" stroke="#1f6fc0" stroke-width="1.4"/></svg>
      </p>
      <p class="contact__line">www.skyvornq.com
        <svg class="contact__icon" viewBox="0 0 16 16"><circle cx="8" cy="8" r="7" fill="#fff"/><path d="M1 8h14M8 1c-3 4-3 10 0 14M8 1c3 4 3 10 0 14" fill="none" stroke="#1f6fc0" stroke-width="1.2"/></svg>
      </p>
    </div>
  </section>

  <section class="card card--back">
    <p class="back__url">www.skyvornq.com</p>
    <div class="back__mark">
      <span class="back__dot"></span>
      <span class="back__name">SkyvornQ</span>
    </div>
  </section>

</main>
</body>
</html>
```